Black Matte card with samurai logo which I would like it to be textured and company name on one side and on the other side I would like the company information with the reno (Face logo) Sushi logo. Double Sided card.

majority customers are University students, University sororities and fraternities.

It Company

Reno Sushi
317 W. Harlow Ave
Tucson, AZ 85042
Phone (520)413-6271
Fax (520)357-1846
E-mail: Renosushidesert@mailbox-example.com
FB: Renosushidesert
Twitter: Renosushidesert

• Present Normal

```html
<!DOCTYPE html>
<html lang="en">
<head>
<meta charset="utf-8">
<title>Reno Sushi – Business Card</title>
<link href="https://fonts.googleapis.com/css2?family=PT+Sans:wght@400;700&display=swap" rel="stylesheet">
<style>
  :root {
    --page-bg: #e9e6e1;
    --card-black: #0d0d0d;
    --card-black-soft: #2a2a2a;
    --card-white: #ffffff;
    --brand-red: #b8282b;
    --ink: #454545;
    --stripe-dark: #1c1c1c;
  }
  * { margin: 0; padding: 0; box-sizing: border-box; }
  html, body {
    width: 1200px;
    height: 1094px;
    overflow: hidden;
    background: var(--page-bg);
    font-family: "PT Sans", Arial, sans-serif;
  }
  .canvas {
    position: relative;
    width: 1200px;
    height: 1094px;
  }

  /* Front side */
  .card-front {
    position: absolute;
    left: 62px;
    top: 74px;
    width: 830px;
    height: 472px;
    background:
      radial-gradient(ellipse at 50% 38%, var(--card-black-soft) 0%, var(--card-black) 62%, #000 100%);
    box-shadow: 0 3px 8px rgba(0,0,0,0.35);
  }
  .front-emblem {
    position: absolute;
    left: 315px;
    top: 128px;
    width: 200px;
    height: 200px;
    border-radius: 50%;
    background: var(--brand-red);
  }
  .front-name {
    position: absolute;
    left: 0;
    right: 0;
    top: 358px;
    text-align: center;
    font-size: 62px;
    font-weight: 400;
    color: var(--brand-red);
    letter-spacing: 1px;
  }

  /* Back side */
  .card-back {
    position: absolute;
    left: 335px;
    top: 581px;
    width: 826px;
    height: 475px;
    background: var(--card-white);
    box-shadow: 0 3px 8px rgba(0,0,0,0.3);
    color: var(--ink);
  }
  .back-stripe {
    position: absolute;
    left: 0;
    top: 0;
    width: 24px;
    height: 475px;
  }
  .back-emblem {
    position: absolute;
    left: 50px;
    top: 38px;
    width: 138px;
    height: 138px;
    border-radius: 50%;
    background: var(--brand-red);
  }
  .back-name {
    position: absolute;
    left: 44px;
    top: 188px;
    width: 160px;
    text-align: center;
    font-size: 42px;
    line-height: 1;
    color: var(--brand-red);
  }
  .contact-list {
    position: absolute;
    left: 38px;
    top: 308px;
    list-style: none;
    font-size: 21px;
  }
  .contact-list li {
    display: flex;
    align-items: center;
    height: 32px;
  }
  .contact-icon {
    width: 18px;
    height: 18px;
    margin-right: 12px;
    fill: var(--brand-red);
  }
  .address {
    position: absolute;
    left: 38px;
    top: 426px;
    font-size: 21px;
  }
  .social-list {
    position: absolute;
    right: 18px;
    top: 346px;
    list-style: none;
    font-size: 21px;
  }
  .social-list li {
    display: flex;
    align-items: center;
    height: 31px;
  }
  .social-mark {
    width: 17px;
    height: 17px;
    margin-right: 10px;
    background: #5b7fb8;
  }
</style>
</head>
<body>
<main class="canvas">

  <section class="card-front" aria-label="Card front">
    <div class="front-emblem" role="img" aria-label="Reno Sushi emblem"></div>
    <p class="front-name">reno sushi</p>
  </section>

  <section class="card-back" aria-label="Card back">
    <svg class="back-stripe" viewBox="0 0 24 475" aria-hidden="true">
      <polygon points="0,0 24,0 24,222 0,268" fill="var(--brand-red)"/>
      <polygon points="0,278 24,232 24,475 0,475" fill="var(--stripe-dark)"/>
    </svg>

    <div class="back-emblem" role="img" aria-label="Reno Sushi emblem"></div>
    <p class="back-name">reno sushi</p>

    <ul class="contact-list">
      <li>
        <svg class="contact-icon" viewBox="0 0 24 24" aria-hidden="true">
          <path d="M6.6 10.8a15.1 15.1 0 0 0 6.6 6.6l2.2-2.2a1 1 0 0 1 1-.25 11.4 11.4 0 0 0 3.6.57 1 1 0 0 1 1 1V20a1 1 0 0 1-1 1A17 17 0 0 1 3 4a1 1 0 0 1 1-1h3.5a1 1 0 0 1 1 1c0 1.25.2 2.45.57 3.57a1 1 0 0 1-.25 1z"/>
        </svg>
        (520)413-6271
      </li>
      <li>
        <svg class="contact-icon" viewBox="0 0 24 24" aria-hidden="true">
          <path d="M7 1h10a2 2 0 0 1 2 2v18a2 2 0 0 1-2 2H7a2 2 0 0 1-2-2V3a2 2 0 0 1 2-2zm0 4v12h10V5zm5 14a1 1 0 1 0 0 2 1 1 0 0 0 0-2z"/>
        </svg>
        (520)357-1846
      </li>
      <li>
        <svg class="contact-icon" viewBox="0 0 24 24" aria-hidden="true">
          <path d="M2 8l10-6 10 6v12a1 1 0 0 1-1 1H3a1 1 0 0 1-1-1zm2 1.2V10l8 5 8-5v-.8l-8 5z"/>
        </svg>
        Renosushidesert@mailbox-example.com
      </li>
    </ul>

    <p class="address">Reno Sushi 317 W. Harlow Ave Tucson, AZ 85042</p>

    <ul class="social-list">
      <li><span class="social-mark" aria-hidden="true"></span>Renosushidesert</li>
      <li><span class="social-mark" aria-hidden="true"></span>Renosushidesert</li>
    </ul>
  </section>

</main>
</body>
</html>
```